Bright Step Path Flyer, eyecatching

Hi,
To give you an idea of the business for design purposes, #BrighttStepPath is predominantly a recruitment and people development business, ran by me dedicated to training & assisting others in achieving extra income (pt or f/t) around their current commitments, people also have the opportunity to build their own business brand with my support. My brand colours are Red, White and Black, and I would like to incorporate the following text;

#BrightStepPath

Recruiting now! Start today & start earning!

Would you like an extra income, for…
A holiday?…A new car?…Lifestyle changes?
(Can you put a tick box or something similar adjacent to each)

Are you facing…
Redundancy? Birth of a new child? Hefty bills?

If so, I have the solution.

Contact Yvonne Darcott today: (can you insert the appropriate icon for each of the contact details)
Tel: 07419 604172
Twitter: @Bright_StepPath
Email: Yvonne@brightsteppath-example.co.uk
Facebook: www.facebook-example.com/yvonbrightsteppath

Target Market(s)

Women aged 25-45 years, possibly busy mums too, wanting to earn additinal income to allow them more choices, be it family time, money, new challenge, meeting new people, personal development

Industry/Entity Type

Health And Wellness

Font styles to use
Serif
Sans Serif
Decorative
Script

Colors
ec1f27
ffffff
000000

Requirements
Must have
• My heels logo, be clear concise and eye catching, I also have the following strap line if you wish to use;
• Empowering other to achieve
• Also I have attached a closeup picture of myself but would ideally only like half my face to appear (leftside) similar to the other picture posted - if you can
Nice to have
• Perhaps adding other forms of graphics, or the 3rd picture I have attached with myself...possibly just the shoes though
Should not have
• Too many colours

```html
<!DOCTYPE html>
<html lang="en">
<head>
<meta charset="utf-8">
<title>Bright Step Path Flyer</title>
<link rel="stylesheet" href="https://fonts.googleapis.com/css2?family=Poiret+One&family=Gloria+Hallelujah&display=swap">
<style>
  :root{
    --red:#ec1f27;
    --white:#ffffff;
    --black:#000000;
    --ink:#222222;
    --rule:#c9d3e6;
    --backdrop:#ffffff;
    --shadow:rgba(0,0,0,.45);
  }
  *{box-sizing:border-box;margin:0;padding:0}
  html,body{width:1200px;height:1000px;overflow:hidden;background:var(--backdrop)}
  .canvas{position:relative;width:1200px;height:1000px}
  .flyer{
    position:absolute;left:285px;top:55px;width:630px;height:890px;
    background:var(--white);
    box-shadow:8px 10px 18px var(--shadow);
    font-family:"Poiret One",sans-serif;color:var(--ink);
  }
  .brand-name{
    position:absolute;left:35px;top:52px;
    font-size:56px;line-height:1;color:var(--black);font-weight:400;
    letter-spacing:-1px;
  }
  .strapline{
    position:absolute;left:37px;top:122px;font-size:29px;color:var(--black);
  }
  .heels-art{
    position:absolute;left:420px;top:15px;width:200px;height:210px;
    background:linear-gradient(135deg,#ffffff 0%,#f1f1f1 45%,#e6b3b5 80%,#ec1f27 100%);
    border-radius:4px;
  }
  .notepad{
    position:absolute;left:105px;top:178px;width:400px;height:505px;
    transform:rotate(-2.5deg);
    background:
      repeating-linear-gradient(to bottom,transparent 0 27px,var(--rule) 27px 28px) 0 50px/100% calc(100% - 50px) no-repeat,
      var(--white);
    box-shadow:3px 5px 10px rgba(0,0,0,.35);
    font-family:"Gloria Hallelujah",cursive;font-size:25px;color:var(--ink);
  }
  .notepad-rings{position:absolute;left:14px;top:-10px;width:372px;height:34px}
  .notepad-body{position:absolute;left:28px;top:66px;right:26px}
  .question{text-align:center;line-height:1.2;margin-bottom:6px}
  .question u{text-decoration-color:var(--red);text-decoration-thickness:3px}
  .checklist{list-style:none;margin-bottom:30px}
  .checklist li{display:flex;justify-content:space-between;align-items:center;height:33px}
  .tick{width:34px;height:32px;flex:none}
  .call-to-action{
    text-align:center;font-size:30px;color:var(--black);margin-top:-4px;
    text-decoration:underline;text-decoration-color:var(--red);text-decoration-thickness:3px;text-underline-offset:6px;
  }
  .headline{
    position:absolute;left:0;right:0;top:690px;text-align:center;
    font-size:46px;color:var(--black);
  }
  .contact-lead{
    position:absolute;left:0;right:0;top:752px;text-align:center;font-size:29px;color:var(--black);
  }
  .contacts{position:absolute;left:18px;right:12px;top:795px;display:flex;flex-wrap:wrap;justify-content:center;gap:10px 26px}
  .contact{display:flex;align-items:center;gap:8px;font-size:21px;color:var(--black);font-weight:700}
  .contact-mark{width:44px;height:30px;flex:none}
</style>
</head>
<body>
<div class="canvas">
  <section class="flyer">
    <h1 class="brand-name">#BrightStepPath</h1>
    <p class="strapline">Empowering others to achieve</p>
    <div class="heels-art" role="img" aria-label="Sketched pair of black high heels with red soles"></div>

    <div class="notepad">
      <svg class="notepad-rings" viewBox="0 0 372 34" aria-hidden="true">
        <g fill="none" stroke="#555" stroke-width="3">
          <path d="M8 30 V12 a5 5 0 0 1 10 0 V22"/><path d="M30 30 V12 a5 5 0 0 1 10 0 V22"/><path d="M52 30 V12 a5 5 0 0 1 10 0 V22"/><path d="M74 30 V12 a5 5 0 0 1 10 0 V22"/><path d="M96 30 V12 a5 5 0 0 1 10 0 V22"/><path d="M118 30 V12 a5 5 0 0 1 10 0 V22"/><path d="M140 30 V12 a5 5 0 0 1 10 0 V22"/><path d="M162 30 V12 a5 5 0 0 1 10 0 V22"/><path d="M184 30 V12 a5 5 0 0 1 10 0 V22"/><path d="M206 30 V12 a5 5 0 0 1 10 0 V22"/><path d="M228 30 V12 a5 5 0 0 1 10 0 V22"/><path d="M250 30 V12 a5 5 0 0 1 10 0 V22"/><path d="M272 30 V12 a5 5 0 0 1 10 0 V22"/><path d="M294 30 V12 a5 5 0 0 1 10 0 V22"/><path d="M316 30 V12 a5 5 0 0 1 10 0 V22"/><path d="M338 30 V12 a5 5 0 0 1 10 0 V22"/><path d="M360 30 V12 a5 5 0 0 1 10 0 V22"/>
        </g>
      </svg>
      <div class="notepad-body">
        <p class="question">Would you like an<br><u>extra income</u>, for…</p>
        <ul class="checklist">
          <li>A holiday?<svg class="tick" viewBox="0 0 34 32"><rect x="2" y="8" width="22" height="22" fill="none" stroke="#111" stroke-width="2.5"/><path d="M6 18 l6 7 L31 3" fill="none" stroke="#ec1f27" stroke-width="4" stroke-linecap="round"/></svg></li>
          <li>A new car?<svg class="tick" viewBox="0 0 34 32"><rect x="2" y="8" width="22" height="22" fill="none" stroke="#111" stroke-width="2.5"/><path d="M6 18 l6 7 L31 3" fill="none" stroke="#ec1f27" stroke-width="4" stroke-linecap="round"/></svg></li>
          <li>Lifestyle changes?<svg class="tick" viewBox="0 0 34 32"><rect x="2" y="8" width="22" height="22" fill="none" stroke="#111" stroke-width="2.5"/><path d="M6 18 l6 7 L31 3" fill="none" stroke="#ec1f27" stroke-width="4" stroke-linecap="round"/></svg></li>
        </ul>
        <p class="question">Are you facing…</p>
        <ul class="checklist">
          <li>Redundancy?<svg class="tick" viewBox="0 0 34 32"><rect x="2" y="8" width="22" height="22" fill="none" stroke="#111" stroke-width="2.5"/><path d="M6 18 l6 7 L31 3" fill="none" stroke="#ec1f27" stroke-width="4" stroke-linecap="round"/></svg></li>
          <li>Birth of a new child?<svg class="tick" viewBox="0 0 34 32"><rect x="2" y="8" width="22" height="22" fill="none" stroke="#111" stroke-width="2.5"/><path d="M6 18 l6 7 L31 3" fill="none" stroke="#ec1f27" stroke-width="4" stroke-linecap="round"/></svg></li>
          <li>Hefty bills?<svg class="tick" viewBox="0 0 34 32"><rect x="2" y="8" width="22" height="22" fill="none" stroke="#111" stroke-width="2.5"/><path d="M6 18 l6 7 L31 3" fill="none" stroke="#ec1f27" stroke-width="4" stroke-linecap="round"/></svg></li>
        </ul>
        <p class="call-to-action">Recruiting now!</p>
      </div>
    </div>

    <p class="headline">Start today &amp; start earning!</p>
    <p class="contact-lead">Contact Yvonne Darcott today:</p>

    <div class="contacts">
      <span class="contact">
        <svg class="contact-mark" viewBox="0 0 44 30" aria-hidden="true"><path d="M2 8 Q20 0 42 5 L40 26 Q18 30 4 24 Z" fill="#ec1f27"/><path d="M12 12 q10 -6 20 0 v3 h-4 v-2 h-12 v2 h-4 z M14 16 h16 l2 8 h-20 z" fill="none" stroke="#111" stroke-width="1.6"/><circle cx="22" cy="20" r="2.5" fill="none" stroke="#111" stroke-width="1.4"/></svg>
        07419 604172
      </span>
      <span class="contact">
        <svg class="contact-mark" viewBox="0 0 44 30" aria-hidden="true"><path d="M2 8 Q20 0 42 5 L40 26 Q18 30 4 24 Z" fill="#ec1f27"/><rect x="11" y="9" width="22" height="14" fill="none" stroke="#111" stroke-width="1.6"/><path d="M11 9 l11 8 l11 -8" fill="none" stroke="#111" stroke-width="1.6"/></svg>
        yvonne@brightsteppath-example.co.uk
      </span>
      <span class="contact">
        <svg class="contact-mark" viewBox="0 0 44 30" aria-hidden="true"><path d="M2 8 Q20 0 42 5 L40 26 Q18 30 4 24 Z" fill="#ec1f27"/></svg>
        yvonbrightsteppath
      </span>
      <span class="contact">
        <svg class="contact-mark" viewBox="0 0 44 30" aria-hidden="true"><path d="M2 8 Q20 0 42 5 L40 26 Q18 30 4 24 Z" fill="#ec1f27"/></svg>
        @Bright_StepPath
      </span>
    </div>
  </section>
</div>
</body>
</html>
```